Structural Engineering Business Card

Brookvane Drafting does residential house plans for clients in Central Florida. Would like simple but elegant business card that is appropriate for a house plan engineering company. Prefer black business card with black/white them but open to other shades of blue. I uploaded a sample card that I came across that looked good but please come up with your own creative designs.

Contact Information for Business Card

Name, Title, Phone, Email, Address, website

```html
<!DOCTYPE html>
<html lang="en">
<head>
<meta charset="utf-8">
<title>Brookvane Drafting – Business Card</title>
<link href="https://fonts.googleapis.com/css2?family=Montserrat:wght@800&family=Quicksand:wght@500&display=swap" rel="stylesheet">
<style>
  :root {
    --backdrop: #c9c9c9;
    --card: #ffffff;
    --ink: #0d0d0d;
    --muted: #555555;
    --shadow: rgba(0,0,0,0.18);
  }
  html, body {
    margin: 0;
    padding: 0;
    width: 1200px;
    height: 1200px;
    overflow: hidden;
    background: var(--backdrop);
  }
  .canvas {
    position: relative;
    width: 1200px;
    height: 1200px;
  }
  .card {
    position: absolute;
    left: 250px;
    width: 700px;
    height: 400px;
    background: var(--card);
    box-shadow: 0 10px 30px var(--shadow);
  }
  .card--front { top: 150px; }
  .card--back { top: 650px; }

  .brand {
    display: flex;
    align-items: center;
    gap: 12px;
    font-family: "Montserrat", sans-serif;
    font-weight: 800;
    color: var(--ink);
    text-transform: uppercase;
    line-height: 1;
  }
  .brand__mark {
    background: var(--ink);
    flex: none;
  }
  .card--front .brand {
    position: absolute;
    left: 50px;
    top: 176px;
    font-size: 22px;
    letter-spacing: 0.5px;
  }
  .card--front .brand__mark { width: 18px; height: 18px; }

  .card--back .brand {
    position: absolute;
    inset: 0;
    justify-content: center;
    font-size: 40px;
    letter-spacing: 1px;
  }
  .card--back .brand__mark { width: 32px; height: 32px; }

  .contact {
    position: absolute;
    left: 395px;
    top: 110px;
    width: 290px;
  }
  .contact__name {
    margin: 0;
    font-family: "Montserrat", sans-serif;
    font-weight: 800;
    font-size: 22px;
    color: var(--ink);
    text-transform: uppercase;
  }
  .contact__title {
    margin: 0 0 24px;
    font-family: "Quicksand", sans-serif;
    font-weight: 500;
    font-size: 16px;
    color: var(--muted);
  }
  .contact__list {
    list-style: none;
    margin: 0;
    padding: 0;
    font-family: "Quicksand", sans-serif;
    font-weight: 500;
    font-size: 17px;
    color: var(--muted);
  }
  .contact__item {
    display: flex;
    align-items: flex-start;
    gap: 10px;
    margin-bottom: 6px;
    line-height: 22px;
  }
  .contact__icon {
    width: 20px;
    height: 20px;
    flex: none;
    margin-top: 1px;
  }
</style>
</head>
<body>
<main class="canvas">

  <section class="card card--front" aria-label="Card front">
    <div class="brand"><span class="brand__mark"></span>Brookvane Drafting</div>

    <div class="contact">
      <h1 class="contact__name">Dorian Kell</h1>
      <p class="contact__title">Owner</p>
      <ul class="contact__list">
        <li class="contact__item">
          <svg class="contact__icon" viewBox="0 0 20 20" aria-hidden="true">
            <circle cx="10" cy="10" r="10" fill="#0d0d0d"/>
            <path d="M7 5.5 L8.6 5.5 L9.3 8 L8.2 8.9 Q9.2 11 11.1 11.8 L12 10.7 L14.5 11.4 L14.5 13 Q14 14.5 12.3 14.3 Q6.5 13.2 5.7 7.5 Q5.6 5.8 7 5.5 Z" fill="#fff"/>
          </svg>
          (555) 014-2290
        </li>
        <li class="contact__item">
          <svg class="contact__icon" viewBox="0 0 20 20" aria-hidden="true">
            <circle cx="10" cy="10" r="10" fill="#0d0d0d"/>
            <rect x="5" y="6.5" width="10" height="7" fill="none" stroke="#fff" stroke-width="1.3"/>
            <path d="M5 6.5 L10 10.5 L15 6.5" fill="none" stroke="#fff" stroke-width="1.3"/>
          </svg>
          hello@brookvane.com
        </li>
        <li class="contact__item">
          <svg class="contact__icon" viewBox="0 0 20 20" aria-hidden="true">
            <circle cx="10" cy="10" r="10" fill="#0d0d0d"/>
            <circle cx="10" cy="10" r="5.5" fill="none" stroke="#fff" stroke-width="1.2"/>
            <ellipse cx="10" cy="10" rx="2.3" ry="5.5" fill="none" stroke="#fff" stroke-width="1.2"/>
            <path d="M4.5 10 H15.5" stroke="#fff" stroke-width="1.2"/>
          </svg>
          www.brookvane.com
        </li>
        <li class="contact__item">
          <svg class="contact__icon" viewBox="0 0 20 20" aria-hidden="true">
            <circle cx="10" cy="10" r="10" fill="#0d0d0d"/>
            <path d="M10 15.5 Q5.8 10.8 5.8 8.4 A4.2 4.2 0 0 1 14.2 8.4 Q14.2 10.8 10 15.5 Z" fill="#fff"/>
            <circle cx="10" cy="8.4" r="1.6" fill="#0d0d0d"/>
          </svg>
          <span>218 Harlow Lane Ocala,<br>FL 34470</span>
        </li>
      </ul>
    </div>
  </section>

  <section class="card card--back" aria-label="Card back">
    <div class="brand"><span class="brand__mark"></span>Brookvane Drafting</div>
  </section>

</main>
</body>
</html>
```